Online business manager needs a website

I need a website designed and then coded. I am an online business manager serving a number of different industries providing administrative support to existing small businesses and helping solo practitioners get their new business up and running.

I didn't have a logo formally designed but have been using the attached avatar and wouldn't mind something that incorporated that.

The business doesn't have an official name, so I've just been using my name Lena Morvath, Online Business Manager or Lena Morvath, OBM. I've attached two documents that I have made previously for an example of content.

I would prefer the final site be in Wordpress.

Requirements
Must have
• A way to contact me, testimonials, list of services

```html
<!DOCTYPE html>
<html lang="en">
<head>
<meta charset="utf-8">
<title>Lena Morvath – Online Business Manager</title>
<link href="https://fonts.googleapis.com/css2?family=Libre+Baskerville:wght@400;700&family=Montserrat:wght@400;500;600;700&display=swap" rel="stylesheet">
<style>
:root{
  --purple:#5a4bc3;
  --purple-deep:#4b3fb4;
  --teal:#23d6c6;
  --cyan:#2bc4df;
  --navy:#2d2a6e;
  --ink:#333;
  --pale:#eef3fd;
  --white:#fff;
  --gold:#f5b800;
}
*{box-sizing:border-box;margin:0;padding:0}
html,body{width:1200px;height:4570px;overflow:hidden}
body{position:relative;font-family:'Montserrat',sans-serif;color:var(--ink);background:var(--white)}
.abs{position:absolute}
.serif{font-family:'Libre Baskerville',serif}
.btn{position:absolute;display:flex;align-items:center;justify-content:center;font-size:11px;font-weight:600;letter-spacing:.5px;border-radius:4px;text-transform:uppercase;white-space:nowrap}
.btn-purple{background:var(--purple);color:#fff}
.btn-teal{background:var(--teal);color:#fff}
.btn-cyan{background:var(--cyan);color:#fff}
.btn-white{background:#fff;color:var(--purple)}
.btn-outline{border:1.5px solid #fff;color:#fff}
.ph{position:absolute}
.title{position:absolute;left:0;width:1200px;text-align:center;font-family:'Libre Baskerville',serif;font-weight:700;font-size:31px;color:var(--navy);white-space:nowrap}
.title .hl{color:var(--teal)}
.title .hl2{color:var(--purple)}

/* hero */
.hero{position:absolute;left:0;top:0;width:1200px;height:598px;background:linear-gradient(100deg,var(--purple-deep) 0%,var(--purple) 48%,#3fb6d6 75%,var(--teal) 100%)}
.brand-name{font-family:'Libre Baskerville',serif;font-size:25px;color:#fff;white-space:nowrap}
.brand-sub{font-size:10px;font-weight:600;color:#fff;white-space:nowrap}
.hero h1{position:absolute;left:92px;top:208px;width:430px;font-family:'Libre Baskerville',serif;font-weight:700;font-size:38px;line-height:60px;color:#fff;white-space:nowrap}
.hero p{position:absolute;left:92px;top:392px;width:440px;font-size:11px;line-height:21px;color:#fff}
.card{position:absolute;background:#fff;border-radius:8px;box-shadow:0 8px 24px rgba(40,40,120,.15)}
.follow{position:absolute;left:1140px;top:326px;transform:rotate(-90deg);transform-origin:left top;font-size:10px;font-weight:600;color:#fff;letter-spacing:1px;white-space:nowrap}

/* about */
.about-text{position:absolute;left:602px;top:772px;width:504px;font-size:11px;line-height:23px;color:var(--ink);text-align:justify}

/* services */
.services{position:absolute;left:0;top:1136px;width:1200px;height:900px;background:var(--pale)}
.svc{position:absolute;width:245px;height:229px;background:#fff;border-radius:8px;box-shadow:0 6px 18px rgba(60,70,140,.08);text-align:center}
.svc .ic{position:absolute;left:78px;top:-44px;width:88px;height:88px;border-radius:50%;border:6px solid #fff;display:flex;align-items:center;justify-content:center;box-shadow:0 4px 12px rgba(0,0,0,.08)}
.svc h3{position:absolute;top:70px;left:0;width:100%;font-family:'Libre Baskerville',serif;font-size:14px;font-weight:700;color:#222}
.svc p{position:absolute;top:102px;left:14px;right:14px;font-size:9.5px;line-height:19px;color:#555}

/* industry */
.logo-box{position:absolute;top:2164px;width:149px;height:94px;background:#fff;border:1px solid #e4e6ef;border-radius:4px;box-shadow:0 4px 12px rgba(0,0,0,.06);display:flex;align-items:center;justify-content:center;font-family:'Montserrat',sans-serif;font-weight:700;font-size:20px;white-space:nowrap}
.arrow{position:absolute;width:26px;height:26px;border-radius:50%;display:flex;align-items:center;justify-content:center}
.arrow-light{border:1px solid #c9cde0;background:#fff}
.arrow-dark{background:var(--purple)}

/* testimonials */
.testi{position:absolute;left:0;top:2329px;width:1200px;height:472px;background:var(--pale);overflow:hidden}
.quote{position:absolute;top:128px;width:444px;height:183px;background:#fff;border-radius:6px;box-shadow:0 6px 18px rgba(60,70,140,.08);text-align:center}
.quote .stars{margin-top:28px;color:var(--gold);font-size:12px;letter-spacing:2px}
.quote p{margin:12px 30px 0;font-size:9.5px;line-height:19px;font-style:italic;color:#444}
.avatar{position:absolute;width:62px;height:62px;border-radius:50%;border:3px solid #fff;background:linear-gradient(135deg,#c9a27c,#7a5339)}
.who{position:absolute;width:444px;text-align:center}
.who b{display:block;font-family:'Libre Baskerville',serif;font-size:14px;color:#222}
.who span{display:block;margin-top:6px;font-family:'Libre Baskerville',serif;font-size:10px;color:var(--purple)}

/* rates */
.rate{position:absolute;top:2929px;width:245px;height:286px;background:#fff;border-radius:8px;box-shadow:0 6px 18px rgba(60,70,140,.1);text-align:center;overflow:hidden}
.rate .head{height:53px;display:flex;align-items:center;justify-content:center;color:#fff;font-family:'Libre Baskerville',serif;font-weight:700;font-size:16px}
.rate .price{margin-top:26px;font-family:'Libre Baskerville',serif;font-weight:700;font-size:29px;color:#111}
.rate .desc{margin:14px 22px 0;font-size:11px;line-height:25px;color:#555}
.rate .note{font-size:9px;font-style:italic;color:#555}
.rate .btn{left:58px;top:218px;width:128px;height:32px}

/* work */
.work{position:absolute;top:3412px;height:325px;border-radius:8px}

/* contact */
.contact{position:absolute;left:92px;top:3808px;width:1016px;height:496px;border-radius:14px;background:linear-gradient(100deg,var(--purple-deep) 0%,var(--purple) 45%,#3cb8d4 78%,var(--teal) 100%)}
.field{position:absolute;background:#fff;border-radius:3px;font-size:9px;color:#555;padding:9px 10px}

/* footer */
.foot-h{position:absolute;font-family:'Libre Baskerville',serif;font-weight:700;font-size:18px;color:var(--teal);white-space:nowrap}
.foot-h .p{color:var(--purple)}
.ci{position:absolute;width:28px;height:28px;border-radius:50%;background:var(--purple);display:flex;align-items:center;justify-content:center}
.ft{position:absolute;font-family:'Libre Baskerville',serif;font-size:11px;color:#222;line-height:17px;white-space:nowrap}
</style>
</head>
<body>

<!-- HERO -->
<section class="hero">
  <div class="ph" role="img" aria-label="Cartoon avatar of the business owner at a laptop" style="left:120px;top:18px;width:56px;height:64px;border-radius:6px;background:linear-gradient(160deg,#f1c46b,#6d7a8f)"></div>
  <div class="abs brand-name" style="left:92px;top:88px">Lena Morvath</div>
  <div class="abs brand-sub" style="left:92px;top:122px">Online Business Manager</div>
  <div class="btn btn-white" style="left:982px;top:59px;width:126px;height:33px">Get Started</div>

  <h1>Start And Grow<br>Your New Business<br>Easily</h1>
  <p>Focused on the live event and entertainment industry. Helping artists and owners to better manage their career and business by strategically reviewing systems, recommending operational efficiencies, and managing inboxes.</p>
  <div class="btn btn-white" style="left:92px;top:477px;width:126px;height:33px">Get Started</div>
  <div class="btn btn-outline" style="left:238px;top:477px;width:126px;height:33px">Contact Us</div>

  <div class="ph" role="img" aria-label="Portrait photo of the business owner smiling" style="left:658px;top:174px;width:354px;height:353px;background:linear-gradient(150deg,#2f4a7a 0%,#b88a5e 45%,#e0b58a 70%,#8f6f52 100%)"></div>

  <div class="card" style="left:532px;top:196px;width:190px;height:138px">
    <div class="abs serif" style="left:16px;top:26px;font-size:12px;color:#222">Growth</div>
    <svg class="abs" style="left:26px;top:48px" width="150" height="70" viewBox="0 0 150 70"><path d="M2 62 C20 30 34 70 54 50 C70 34 80 54 96 40 C112 26 124 36 146 12" stroke="#333" stroke-width="2" fill="none"/><circle cx="54" cy="50" r="3" fill="#5a4bc3"/><circle cx="96" cy="40" r="3" fill="#23d6c6"/></svg>
  </div>

  <div class="card" style="left:939px;top:466px;width:233px;height:88px">
    <div class="abs serif" style="left:22px;top:16px;font-size:12px;font-weight:700;color:#222;white-space:nowrap">12k Reviews On</div>
    <div class="abs" style="left:144px;top:14px;font-size:12px;color:var(--gold);letter-spacing:1px">★★★★★</div>
    <svg class="abs" style="left:20px;top:44px" width="26" height="22" viewBox="0 0 26 22"><path d="M2 20 C4 10 12 6 20 6 M14 1 L21 6 L15 12" stroke="#23d6c6" stroke-width="3" fill="none" stroke-linecap="round"/></svg>
    <div class="abs serif" style="left:52px;top:42px;font-size:20px;font-weight:700;color:#222">4.3</div>
    <div class="abs" style="left:116px;top:42px;width:26px;height:26px;border-radius:50%;border:2px solid #fff;background:#c79a72"></div>
    <div class="abs" style="left:134px;top:42px;width:26px;height:26px;border-radius:50%;border:2px solid #fff;background:#9a6e4c"></div>
    <div class="abs" style="left:152px;top:42px;width:26px;height:26px;border-radius:50%;border:2px solid #fff;background:#d9b08c"></div>
    <div class="abs" style="left:170px;top:40px;width:30px;height:30px;border-radius:50%;border:2px solid #fff;background:var(--purple);color:#fff;font-size:8px;font-weight:700;display:flex;align-items:center;justify-content:center">12k</div>
  </div>

  <div class="abs" style="left:1140px;top:168px;width:14px;height:14px;border-radius:3px;background:#fff"></div>
  <div class="abs" style="left:1140px;top:196px;width:14px;height:14px;border-radius:50%;background:#fff"></div>
  <div class="follow">FOLLOW US ON</div>
  <div class="abs" style="left:1147px;top:340px;width:1px;height:86px;background:#fff"></div>
</section>

<!-- ABOUT -->
<section>
  <div class="ph" style="left:100px;top:700px;width:260px;height:260px;border-radius:50%;background:radial-gradient(circle,#e5dcf7 0%,rgba(255,255,255,0) 70%)"></div>
  <div class="ph" role="img" aria-label="Photo of a business team meeting around a table" style="left:284px;top:669px;width:281px;height:219px;border-radius:6px;background:linear-gradient(135deg,#d7dde6,#6f7f96 60%,#2e3a4e)"></div>
  <div class="ph" role="img" aria-label="Photo of a group of professionals in suits" style="left:76px;top:781px;width:284px;height:243px;border-radius:6px;border:5px solid #fff;background:linear-gradient(135deg,#eef2f6,#95a3b5 55%,#263245)"></div>
  <div class="card" style="left:376px;top:905px;width:167px;height:160px;border-radius:4px">
    <div class="ph" role="img" aria-label="Cartoon avatar of the business owner at a laptop" style="left:30px;top:28px;width:107px;height:104px;border-radius:6px;background:linear-gradient(160deg,#f1c46b,#8fb3c2 55%,#5d6470)"></div>
  </div>

  <div class="abs serif" style="left:602px;top:722px;font-size:31px;font-weight:700;color:var(--teal);white-space:nowrap">About <span style="color:var(--purple)">Lena Morvath</span></div>
  <p class="about-text">Hi! I'm so excited that you have chosen to explore my portfolio. Helping businesses achieve their goals is my passion, and I'm thrilled that with my assistance you will have more time for your own passion project. I thrive while working independently, which means you can be confident when leaving tasks for me. The type of work that lights me up is anything involving organization and/or spreadsheets. Think complex data analyzed that includes multiple nested if formulas? You have an overwhelming amount of email to sort through and appointments to book? I'm your gal!</p>
  <div class="btn btn-purple" style="left:602px;top:953px;width:126px;height:33px">Contact Us</div>
</section>

<!-- SERVICES -->
<section class="services">
  <div class="title" style="top:66px">Lena Morvath <span class="hl">Services</span></div>
  <p class="abs" style="left:250px;top:128px;width:700px;text-align:center;font-size:11px;line-height:22px;color:#444">There are many variations of passages of Lorem Ipsum available, but the majority have suffered alteration in some form, by injected humour, or randomised words which don't look even slightly believable</p>

  <div class="svc" style="left:92px;top:241px"><div class="ic" style="background:var(--purple)"><svg width="34" height="34" viewBox="0 0 34 34"><circle cx="17" cy="17" r="13" stroke="#fff" stroke-width="2" fill="none"/><circle cx="17" cy="17" r="4" stroke="#fff" stroke-width="2" fill="none"/><path d="M17 4 V9 M17 25 V30 M4 17 H9 M25 17 H30" stroke="#fff" stroke-width="2"/></svg></div><h3>Content Repurposing</h3><p>It is a long established fact that a reader will be distracted by the readable content of a page when looking at its layout. The point of using Lorem Ipsum is that it has a more-or-less normal.</p></div>
  <div class="svc" style="left:350px;top:241px"><div class="ic" style="background:var(--teal)"><svg width="34" height="34" viewBox="0 0 34 34"><path d="M5 30 H30 M8 28 V20 M14 28 V14 M20 28 V17 M26 28 V9" stroke="#fff" stroke-width="3"/><path d="M6 16 L14 9 L20 12 L29 4" stroke="#fff" stroke-width="2" fill="none"/></svg></div><h3>Financial Analytics</h3><p>It is a long established fact that a reader will be distracted by the readable content of a page when looking at its layout. The point of using Lorem Ipsum is that it has a more-or-less normal.</p></div>
  <div class="svc" style="left:605px;top:241px"><div class="ic" style="background:var(--cyan)"><svg width="34" height="34" viewBox="0 0 34 34"><rect x="5" y="5" width="24" height="18" rx="2" stroke="#fff" stroke-width="2" fill="none"/><path d="M12 29 H22 M17 23 V29 M10 11 H24 M10 16 H20" stroke="#fff" stroke-width="2"/></svg></div><h3>Data Entry</h3><p>It is a long established fact that a reader will be distracted by the readable content of a page when looking at its layout. The point of using Lorem Ipsum is that it has a more-or-less normal.</p></div>
  <div class="svc" style="left:863px;top:241px"><div class="ic" style="background:var(--purple)"><svg width="34" height="34" viewBox="0 0 34 34"><rect x="5" y="5" width="16" height="16" stroke="#fff" stroke-width="2" fill="none"/><path d="M8 28 L20 16 M26 6 C30 10 30 14 26 16 C22 14 22 10 26 6 Z" stroke="#fff" stroke-width="2" fill="none"/></svg></div><h3>Graphic Creations</h3><p>It is a long established fact that a reader will be distracted by the readable content of a page when looking at its layout. The point of using Lorem Ipsum is that it has a more-or-less normal.</p></div>

  <div class="svc" style="left:92px;top:538px"><div class="ic" style="background:var(--teal)"><svg width="34" height="34" viewBox="0 0 34 34"><rect x="4" y="10" width="26" height="18" rx="2" stroke="#fff" stroke-width="2" fill="none"/><path d="M4 12 L17 21 L30 12" stroke="#fff" stroke-width="2" fill="none"/><circle cx="17" cy="7" r="4" stroke="#fff" stroke-width="2" fill="none"/></svg></div><h3>Email Management</h3><p>It is a long established fact that a reader will be distracted by the readable content of a page when looking at its layout. The point of using Lorem Ipsum is that it has a more-or-less normal.</p></div>
  <div class="svc" style="left:350px;top:538px"><div class="ic" style="background:var(--cyan)"><svg width="34" height="34" viewBox="0 0 34 34"><circle cx="11" cy="11" r="5" stroke="#fff" stroke-width="2" fill="none"/><circle cx="24" cy="22" r="6" stroke="#fff" stroke-width="2" fill="none"/><path d="M4 28 C4 20 18 20 18 24 M24 4 V10" stroke="#fff" stroke-width="2" fill="none"/></svg></div><h3>Project Management</h3><p>It is a long established fact that a reader will be distracted by the readable content of a page when looking at its layout. The point of using Lorem Ipsum is that it has a more-or-less normal.</p></div>
  <div class="svc" style="left:605px;top:538px"><div class="ic" style="background:var(--purple)"><svg width="34" height="34" viewBox="0 0 34 34"><rect x="6" y="4" width="18" height="24" rx="2" stroke="#fff" stroke-width="2" fill="none"/><path d="M10 10 H20 M10 15 H20 M10 20 H16" stroke="#fff" stroke-width="2"/><circle cx="26" cy="24" r="5" stroke="#fff" stroke-width="2" fill="none"/></svg></div><h3>Bookkeeping</h3><p>It is a long established fact that a reader will be distracted by the readable content of a page when looking at its layout. The point of using Lorem Ipsum is that it has a more-or-less normal.</p></div>
  <div class="svc" style="left:863px;top:538px"><div class="ic" style="background:var(--teal)"><svg width="34" height="34" viewBox="0 0 34 34"><path d="M6 30 V18 H12 V30 M12 20 L18 14 C20 12 22 14 20 17 H28 C30 17 30 21 28 21 L24 30 H12" stroke="#fff" stroke-width="2" fill="none"/><path d="M24 3 V9 M21 6 H27" stroke="#fff" stroke-width="2"/></svg></div><h3>More Awesomeness</h3><p>It is a long established fact that a reader will be distracted by the readable content of a page when looking at its layout. The point of using Lorem Ipsum is that it has a more-or-less normal.</p></div>

  <div class="btn btn-purple" style="left:550px;top:795px;width:126px;height:33px">Contact Us</div>
</section>

<!-- INDUSTRY -->
<section>
  <div class="title" style="top:2102px;color:var(--teal)">Industry <span class="hl2">Lena Morvath Serve</span></div>
  <div class="arrow arrow-light" style="left:42px;top:2198px"><svg width="8" height="10" viewBox="0 0 8 10"><path d="M6 1 L2 5 L6 9" stroke="#888" stroke-width="1.5" fill="none"/></svg></div>
  <div class="logo-box" style="left:92px;color:#1d4fa0">Harborline</div>
  <div class="logo-box" style="left:265px;color:#222">Stratafield</div>
  <div class="logo-box" style="left:438px;color:#333;font-size:17px">Azure Lodges</div>
  <div class="logo-box" style="left:612px;color:#e2231a">Voxa</div>
  <div class="logo-box" style="left:786px;color:#1a8fd6">Kelvo</div>
  <div class="logo-box" style="left:958px;color:#e31e24">Tally9</div>
  <div class="arrow arrow-dark" style="left:1130px;top:2198px"><svg width="8" height="10" viewBox="0 0 8 10"><path d="M2 1 L6 5 L2 9" stroke="#fff" stroke-width="1.5" fill="none"/></svg></div>
</section>

<!-- TESTIMONIALS -->
<section class="testi">
  <div class="title" style="top:62px">What Client's Say <span class="hl">About Lena</span></div>

  <div class="quote" style="left:-330px;opacity:.45"><div class="stars">★★★★★</div><p>"When it became apparent that a project would take more time than I had, she stepped up to take on the required research. She was thorough and timely; able to meet a last-minute 12-hour deadline. I would highly recommend her to assist with your next project."</p></div>
  <div class="quote" style="left:142px"><div class="stars">★★★★★</div><p>"When it became apparent that a project would take more time than I had, Lena stepped up to take on the required research. She was thorough and timely; able to meet a last-minute 12-hour deadline. I would highly recommend Lena to assist with your next project."</p></div>
  <div class="quote" style="left:614px"><div class="stars">★★★★★</div><p>"When it became apparent that a project would take more time than I had, Lena stepped up to take on the required research. She was thorough and timely; able to meet a last-minute 12-hour deadline. I would highly recommend Lena to assist with your next project."</p></div>
  <div class="quote" style="left:1086px;opacity:.45"><div class="stars">★★★★★</div><p>"When it became apparent that a project would take more time than I had, she stepped up to take on the required research. She was thorough and timely; able to meet a last-minute 12-hour deadline."</p></div>

  <div class="arrow arrow-light" style="left:44px;top:208px"><svg width="8" height="10" viewBox="0 0 8 10"><path d="M6 1 L2 5 L6 9" stroke="#888" stroke-width="1.5" fill="none"/></svg></div>
  <div class="arrow arrow-dark" style="left:1130px;top:208px"><svg width="8" height="10" viewBox="0 0 8 10"><path d="M2 1 L6 5 L2 9" stroke="#fff" stroke-width="1.5" fill="none"/></svg></div>

  <div class="avatar" role="img" aria-label="Client portrait" style="left:333px;top:280px"></div>
  <div class="avatar" role="img" aria-label="Client portrait" style="left:805px;top:280px"></div>
  <div class="who" style="left:142px;top:362px"><b>Noa R.</b><span>Owner, Brightridge Homes</span></div>
  <div class="who" style="left:614px;top:362px"><b>Noa R.</b><span>Owner, Brightridge Homes</span></div>
</section>

<!-- RATES -->
<section>
  <div class="title" style="top:2865px;color:var(--teal)">Rates And Packages <span class="hl2">Of Lena Morvath</span></div>
  <div class="rate" style="left:92px"><div class="head" style="background:var(--purple)">Hourly Rate</div><div class="price">$40</div><div class="desc">For clients needing only occasional help</div><div class="btn btn-purple">Get Started</div></div>
  <div class="rate" style="left:350px"><div class="head" style="background:var(--teal)">20 hours/month</div><div class="price">$700</div><div class="desc">Includes one 15 minute meeting per week<br><span class="note">(Responses within 72 hours)</span></div><div class="btn btn-teal">Get Started</div></div>
  <div class="rate" style="left:605px"><div class="head" style="background:var(--cyan)">40 hours/month</div><div class="price">$1,300</div><div class="desc">Includes one 30 minute meeting per week<br><span class="note">(Responses within 48 hours)</span></div><div class="btn btn-cyan">Get Started</div></div>
  <div class="rate" style="left:863px"><div class="head" style="background:var(--purple)">20 hours/month</div><div class="price">$2,400</div><div class="desc">Includes one 60 minute meeting per week<br><span class="note">(Responses within 24 hours)</span></div><div class="btn btn-purple">Get Started</div></div>
</section>

<!-- WORK -->
<section>
  <div class="title" style="top:3349px">Lena Morvath <span class="hl">Work</span></div>
  <div class="arrow arrow-light" style="left:44px;top:3562px"><svg width="8" height="10" viewBox="0 0 8 10"><path d="M6 1 L2 5 L6 9" stroke="#888" stroke-width="1.5" fill="none"/></svg></div>
  <div class="work" role="img" aria-label="Podcast promo graphic with two host portraits on a peach background" style="left:92px;width:325px;background:linear-gradient(135deg,#fbeee4,#f4d9c6 60%,#e7b79a)"></div>
  <div class="work" role="img" aria-label="Podcast episode cover with a guest portrait framed in navy" style="left:440px;width:320px;border:8px solid #2a2a6b;background:#f6f1ea"></div>
  <div class="work" role="img" aria-label="Blog header of a pink desk with a keyboard and notebook" style="left:783px;width:325px;background:linear-gradient(135deg,#efc9cf,#e6b8bf 60%,#f5f2ee)"></div>
  <div class="arrow arrow-dark" style="left:1130px;top:3562px"><svg width="8" height="10" viewBox="0 0 8 10"><path d="M2 1 L6 5 L2 9" stroke="#fff" stroke-width="1.5" fill="none"/></svg></div>
</section>

<!-- CONTACT -->
<section class="contact">
  <div class="abs serif" style="left:46px;top:116px;font-size:26px;font-weight:700;color:#fff;white-space:nowrap">Get In Touch With Lena Morvath</div>
  <div class="field" style="left:46px;top:172px;width:226px;height:32px">First Name*</div>
  <div class="field" style="left:290px;top:172px;width:224px;height:32px">Last Name*</div>
  <div class="field" style="left:46px;top:220px;width:226px;height:32px">Phone Number*</div>
  <div class="field" style="left:290px;top:220px;width:224px;height:32px">Email*</div>
  <div class="field" style="left:46px;top:268px;width:468px;height:71px">Message*</div>
  <div class="btn btn-white" style="left:46px;top:367px;width:127px;height:34px">Submit</div>
  <div class="ph" role="img" aria-label="Cartoon avatar of the business owner waving from a laptop screen" style="left:556px;top:70px;width:426px;height:382px;border-radius:10px;background:linear-gradient(160deg,#f3c96a 0%,#8cc3cf 45%,#4a7d6a 70%,#9aa0aa 100%)"></div>
</section>

<!-- FOOTER -->
<footer>
  <div class="foot-h" style="left:92px;top:4360px">Contact <span class="p">Us</span></div>
  <div class="ci" style="left:92px;top:4405px"><svg width="14" height="14" viewBox="0 0 14 14"><path d="M3 1 L5 4 L4 6 C5 8 6 9 8 10 L10 9 L13 11 L12 13 C6 13 1 8 1 2 Z" fill="#fff"/></svg></div>
  <div class="ft" style="left:130px;top:4401px"><b>Call Us</b><br>555.014.2287</div>
  <div class="ci" style="left:92px;top:4455px"><svg width="14" height="12" viewBox="0 0 14 12"><rect x="1" y="1" width="12" height="10" rx="1" stroke="#fff" stroke-width="1.5" fill="none"/><path d="M1 2 L7 7 L13 2" stroke="#fff" stroke-width="1.5" fill="none"/></svg></div>
  <div class="ft" style="left:130px;top:4451px"><b>Email</b><br>hello@lenamorvath.example</div>

  <div class="ph" role="img" aria-label="Cartoon avatar of the business owner at a laptop" style="left:574px;top:4350px;width:72px;height:84px;border-radius:6px;background:linear-gradient(160deg,#f1c46b,#6d7a8f)"></div>
  <div class="abs serif" style="left:480px;top:4440px;width:260px;text-align:center;font-size:25px;color:#222;white-space:nowrap">Lena Morvath</div>
  <div class="abs" style="left:480px;top:4476px;width:260px;text-align:center;font-size:10px;font-weight:600;color:var(--purple)">Online Business Manager</div>

  <div class="foot-h" style="left:985px;top:4360px">Follow <span class="p">Us On</span></div>
  <div class="ci" style="left:985px;top:4405px"></div>
  <div class="ft" style="left:1022px;top:4411px">Friendspace</div>
  <div class="ci" style="left:985px;top:4455px"></div>
  <div class="ft" style="left:1022px;top:4461px">Workline</div>

  <div class="abs" style="left:92px;top:4528px;width:1016px;height:1px;background:#ddd"></div>
  <div class="abs" style="left:0;top:4546px;width:1200px;text-align:center;font-size:9px;color:#333">© 2023 Lena Morvath. All Rights Reserved.</div>
</footer>

</body>
</html>
```